Webdesign for large cottage directory

We have developed a first version of a website that can accommodate large groups (10 to 300 people). The site is English and is aimed at a wide audience ranging from a group of students to a family or a family. For the visitors the site is free and it is the propietaires who pay to see their accommodation. The site is online with just a few fake lodgings and a simple design to the elements that must be appraised (nothing to keep the current design). Our website is here: 9lodgia.com (login / pass = admin / 123) Home page (9lodgia.com): on this page section) and lodging by theme (third section). These three points should be highlighted as possible. The displayed map may be slightly modified. Only the background and the color changes when hovering over the mouse. It can be enlarged / retreciated. Below these 3 sections we have some fairly published articles, the latest blog posts and the footer. The menu will be visible throughout the site. Category page (https://9lodgia.fr/gite-departement/aveyron OR https://9lodgia.fr/gites-couchages-121): On these pages we always return the same format with the googlemap, an image 1 text. Below the list of the cottages concerned and the filter options. Product page: The pages presenting the cottages can be of two types: - Either the cottage has no owner and there is no contact for the visitor to the owner that he can retrieve his cottage by registering: example of a page of this type: https://9lodgia.fr/domaine-de-vercasse - The cottage to a propietaire and we are on the classic card. : // 9lodgia. en / domain-of-vercasse2 For all products on the site we have nav tab. It's just for testing. We do not want to be in the design for real website. All information must be in the page without login / register page: classic, it's here: https://9lodgia.it/login and https://9lodgia.fr/register Blog homepage (https://9lodgia.fr/blog ): Classic blog page Blog post (https://9lodgia.fr/blog/urltemporaire1551521154) and static page (https://9lodgia.fr/blog/Systeme-classement-9lodgiafr): Nothing special Menu: Menu is an important part of the website. It's the way to navigate on the wbesite.
Faible participation designers
4 page

```html
<!DOCTYPE html>
<html lang="en">
<head>
<meta charset="utf-8">
<title>9LODGIA.FR – Home</title>
<link href="https://fonts.googleapis.com/css2?family=Lato:wght@400;700;900&display=swap" rel="stylesheet">
<style>
:root{
  --blue:#1f6fbf;
  --orange:#f06a10;
  --green:#2f9a5e;
  --ink:#222;
  --text:#555;
  --grey-bg:#ececec;
  --footer-bg:#f3f3f3;
  --bar-bg:#333;
  --white:#fff;
}
*{box-sizing:border-box;margin:0;padding:0}
html,body{width:1200px;height:3974px;overflow:hidden}
body{font-family:'Lato',Arial,sans-serif;color:var(--text);background:var(--white);position:relative}
section,header,footer{position:relative;width:1200px}
.section-title{font-weight:900;color:var(--ink);font-size:28px;text-align:center;text-transform:uppercase;letter-spacing:.3px}

/* header */
.site-header{height:87px;display:flex;align-items:center;padding:0 74px}
.brand{font-weight:900;font-size:30px;color:var(--ink);letter-spacing:.3px}
.main-nav{display:flex;gap:28px;margin-left:88px;font-size:15px;color:#333}
.owner-btn{margin-left:auto;background:var(--blue);color:var(--white);font-weight:700;font-size:13px;padding:10px 16px;text-transform:uppercase}

/* hero */
.hero{height:575px;background:linear-gradient(180deg,#7fa9d6 0%,#b9cde0 30%,#8a5a35 55%,#6d8a4a 78%,#4e6a33 100%);display:flex;flex-direction:column;align-items:center;justify-content:center;color:var(--white);text-align:center}
.hero h1{font-weight:900;line-height:1}
.hero .welcome{display:block;font-size:38px;margin-bottom:8px}
.hero .hero-name{display:block;font-size:80px}

/* capacity */
.capacity{height:358px;padding-top:42px}
.capacity-list{display:flex;justify-content:space-between;padding:0 78px;margin-top:42px}
.capacity-item{width:140px;text-align:center}
.capacity-badge{width:130px;height:130px;margin:5px auto 0;border-radius:50%;background:var(--green);border:5px solid var(--white);box-shadow:0 0 0 5px var(--green);display:flex;align-items:center;justify-content:center;color:var(--white);font-weight:900;font-size:42px}
.capacity-label{margin-top:20px;font-size:20px;color:var(--ink);line-height:1.25}

/* department */
.department{height:636px;background:radial-gradient(ellipse at 50% 110%,#6a6a6a 0%,#3a3a3a 45%,#262626 100%);padding-top:56px}
.department .section-title{color:var(--white)}
.dept-map{position:absolute;left:463px;top:106px;width:345px;height:477px;background:#f2f2f2;border-radius:40% 45% 35% 40%}
.dept-tag{position:absolute;left:622px;top:124px;background:var(--orange);color:var(--white);font-size:12px;font-weight:700;padding:5px 14px}

/* theme */
.theme{height:516px;padding-top:36px}
.theme-grid{position:absolute;left:74px;top:98px;width:1050px;display:grid;grid-template-columns:repeat(4,252px);grid-template-rows:161px 161px;column-gap:14px;row-gap:21px}
.theme-tile{display:flex;align-items:center;justify-content:center;color:var(--white);font-weight:900;font-size:18px;text-transform:uppercase;text-align:center}
.t-seminar{background:linear-gradient(135deg,#6b5a48,#cfc7bc)}
.t-peach{background:linear-gradient(180deg,#c58a4a,#3e2c1d)}
.t-aquatic{background:linear-gradient(180deg,#1b5a86,#0f3552)}
.t-bike{background:linear-gradient(180deg,#6f7f8c,#7a5a33)}
.t-horse{background:linear-gradient(135deg,#2c2c2c,#8a8a80)}
.t-gastro{background:linear-gradient(180deg,#3d2a22,#8a3d2a)}
.t-camp{background:linear-gradient(180deg,#51678a,#3e6b49)}
.t-weekend{background:linear-gradient(135deg,#9a3d3a,#d98a5a)}
.theme-arrow{position:absolute;top:1909px}
.arrow-left{left:46px}
.arrow-right{left:1138px}

/* ads */
.ads{height:986px;background:var(--grey-bg);padding-top:50px}
.ad-list{position:absolute;left:74px;top:114px;width:1052px}
.ad-card{display:flex;background:var(--white);height:270px;margin-bottom:14px}
.ad-photo{width:331px;height:270px;flex:none}
.ad-photo-1{background:linear-gradient(180deg,#3a4a6a,#6b3e1f)}
.ad-photo-2{background:linear-gradient(180deg,#5a4a36,#c9c6c0)}
.ad-photo-3{background:linear-gradient(180deg,#d8d8d8,#9aa4b0)}
.ad-body{padding:32px 24px 0 22px;font-size:15px;line-height:28px}
.ad-title{color:var(--blue);font-weight:900;font-size:20px;text-transform:uppercase;margin-bottom:6px}
.ad-label{color:var(--orange);font-weight:700}
.ad-fav{display:inline-block;margin-top:12px;background:var(--blue);color:var(--white);font-weight:700;font-size:13px;text-transform:uppercase;padding:0 16px;line-height:36px}

/* blog */
.blog{height:484px;padding-top:40px}
.blog .section-title{text-align:left;padding-left:74px}
.blog-grid{position:absolute;left:74px;top:95px;display:grid;grid-template-columns:repeat(3,331px);column-gap:29px}
.blog-photo{height:183px}
.b1{background:linear-gradient(180deg,#8fb3d9,#8a5a3a)}
.b2{background:linear-gradient(180deg,#c9d7e0,#5a6a3a)}
.b3{background:linear-gradient(180deg,#6d93c4,#4f7a3a)}
.blog-title{color:var(--blue);font-weight:900;font-size:20px;text-transform:uppercase;margin-top:20px}
.blog-text{font-size:15px;line-height:22px;margin-top:8px}
.read-more{display:block;color:var(--orange);font-weight:700;font-size:12px;text-transform:uppercase;margin-top:22px}

/* footer */
.site-footer{height:271px;background:var(--footer-bg)}
.footer-col{position:absolute;top:58px}
.footer-col h3{color:var(--blue);font-weight:900;font-size:16px;text-transform:uppercase;margin-bottom:10px}
.col-about{left:74px;width:300px;font-size:14px;line-height:22px}
.col-links{left:442px;font-size:14px;line-height:29px}
.col-links ul{list-style:none}
.col-signup{left:705px}
.signup-row{display:flex;gap:13px}
.signup-input{width:241px;height:38px;border:1px solid #ccc;background:var(--white);font-size:13px;color:#777;padding:11px 12px}
.signup-btn{width:101px;height:38px;background:var(--orange);color:var(--white);font-weight:700;font-size:13px;display:flex;align-items:center;justify-content:center;text-transform:uppercase}
.follow{margin-top:22px}
.social{display:flex;gap:20px;margin-top:4px}
.social span{width:18px;height:18px;background:#444;border-radius:3px}
.copyright{height:61px;background:var(--bar-bg);color:#ddd;font-size:12px;display:flex;align-items:center;justify-content:center}
</style>
</head>
<body>

<header class="site-header">
  <div class="brand">9LODGIA.FR</div>
  <nav class="main-nav">
    <span>Cottage by capacity</span>
    <span>Cottage by department</span>
    <span>Lodging by theme</span>
    <span>Blog</span>
    <span>Your Favorites</span>
  </nav>
  <span class="owner-btn">Owner area</span>
</header>

<section class="hero" role="img" aria-label="Large wooden log cottage with a garden and lawn under a blue sky">
  <h1><span class="welcome">WELCOME TO</span><span class="hero-name">9LODGIA.FR</span></h1>
</section>

<section class="capacity">
  <h2 class="section-title">Lodging by capacity</h2>
  <div class="capacity-list">
    <div class="capacity-item"><div class="capacity-badge">1-20</div><p class="capacity-label">2 à 20<br>personnes</p></div>
    <div class="capacity-item"><div class="capacity-badge">1-20</div><p class="capacity-label">20 à 40<br>personnes</p></div>
    <div class="capacity-item"><div class="capacity-badge">1-20</div><p class="capacity-label">40 à 60<br>personnes</p></div>
    <div class="capacity-item"><div class="capacity-badge">1-20</div><p class="capacity-label">60 à 80<br>personnes</p></div>
    <div class="capacity-item"><div class="capacity-badge">1-20</div><p class="capacity-label">80 à 120<br>personnes</p></div>
    <div class="capacity-item"><div class="capacity-badge">1-20</div><p class="capacity-label">+ de 120<br>personnes</p></div>
  </div>
</section>

<section class="department">
  <h2 class="section-title">Lodging by department</h2>
  <div class="dept-map" role="img" aria-label="Clickable map of France divided into departments"></div>
  <span class="dept-tag">AISNE</span>
</section>

<section class="theme">
  <h2 class="section-title">Lodging by theme</h2>
  <div class="theme-grid">
    <div class="theme-tile t-seminar" role="img" aria-label="Seminar photo">Seminar</div>
    <div class="theme-tile t-peach" role="img" aria-label="Fishing at sunset photo">Peach</div>
    <div class="theme-tile t-aquatic" role="img" aria-label="Underwater photo">Aquatic</div>
    <div class="theme-tile t-bike" role="img" aria-label="Mountain bike photo">Mountain bike</div>
    <div class="theme-tile t-horse" role="img" aria-label="Horse riding photo">Horse riding</div>
    <div class="theme-tile t-gastro" role="img" aria-label="Restaurant dining photo">Gastronomic</div>
    <div class="theme-tile t-camp" role="img" aria-label="Summer camp tents photo">Summer camp</div>
    <div class="theme-tile t-weekend" role="img" aria-label="Group party photo">Integration weekend</div>
  </div>
</section>
<svg class="theme-arrow arrow-left" width="16" height="26" viewBox="0 0 16 26"><path d="M13 2 3 13l10 11" fill="none" stroke="#333" stroke-width="3"/></svg>
<svg class="theme-arrow arrow-right" width="16" height="26" viewBox="0 0 16 26"><path d="M3 2l10 11L3 24" fill="none" stroke="#333" stroke-width="3"/></svg>

<section class="ads">
  <h2 class="section-title">Latest ads published</h2>
  <div class="ad-list">
    <article class="ad-card">
      <div class="ad-photo ad-photo-1" role="img" aria-label="Wooden cottage lit at dusk"></div>
      <div class="ad-body">
        <h3 class="ad-title">Maecenas dignissim arcu</h3>
        <p><span class="ad-label">Address:</span> B-12, Meridian Court, Rue des Tilleuls, Lyon 69002, France</p>
        <p><span class="ad-label">Region:</span> Guadeloupe &nbsp; <span class="ad-label">Department:</span> Guadeloupe &nbsp; <span class="ad-label">Capacity:</span> 13</p>
        <p><span class="ad-label">Proposed Formula:</span> Curabitur a risus tempus</p>
        <p><span class="ad-label">Description:</span> Cras viverra velit vitae lorem viverra, non facilisis massa suscipit. Quisque congue aliquam commodo. Duis fermentum euismod neque, et elementum diam porttitor vitae.</p>
        <span class="ad-fav">Add to favorites</span>
      </div>
    </article>
    <article class="ad-card">
      <div class="ad-photo ad-photo-2" role="img" aria-label="Field in winter with a sign"></div>
      <div class="ad-body">
        <h3 class="ad-title">Field of Vercasse222222</h3>
        <p><span class="ad-label">Address:</span> B-12, Meridian Court, Rue des Tilleuls, Lyon 69002, France</p>
        <p><span class="ad-label">Region:</span> Guadeloupe &nbsp; <span class="ad-label">Department:</span> Guadeloupe &nbsp; <span class="ad-label">Capacity:</span> 13</p>
        <p><span class="ad-label">Proposed Formula:</span> Curabitur a risus tempus</p>
        <p><span class="ad-label">Description:</span> Cras viverra velit vitae lorem viverra, non facilisis massa suscipit. Quisque congue aliquam commodo. Duis fermentum euismod neque, et elementum diam porttitor vitae.</p>
        <span class="ad-fav">Add to favorites</span>
      </div>
    </article>
    <article class="ad-card">
      <div class="ad-photo ad-photo-3" role="img" aria-label="Screenshot placeholder image"></div>
      <div class="ad-body">
        <h3 class="ad-title">Field of Vercasse</h3>
        <p><span class="ad-label">Address:</span> B-12, Meridian Court, Rue des Tilleuls, Lyon 69002, France</p>
        <p><span class="ad-label">Region:</span> Guadeloupe &nbsp; <span class="ad-label">Department:</span> Guadeloupe &nbsp; <span class="ad-label">Capacity:</span> 13</p>
        <p><span class="ad-label">Proposed Formula:</span> Curabitur a risus tempus</p>
        <p><span class="ad-label">Description:</span> Cras viverra velit vitae lorem viverra, non facilisis massa suscipit. Quisque congue aliquam commodo. Duis fermentum euismod neque, et elementum diam porttitor vitae.</p>
        <span class="ad-fav">Add to favorites</span>
      </div>
    </article>
  </div>
</section>

<section class="blog">
  <h2 class="section-title">Latest blog posts</h2>
  <div class="blog-grid">
    <article>
      <div class="blog-photo b1" role="img" aria-label="Country house by a lake in autumn"></div>
      <h3 class="blog-title">Maecenas dignissim arcu</h3>
      <p class="blog-text">Aliquam sit amet faucibus maurisvivamus nibh risus, malesuada et ipsum in, iaculis feugiat quam vitae placerat consectetur..</p>
      <span class="read-more">Read more &gt;&gt;</span>
    </article>
    <article>
      <div class="blog-photo b2" role="img" aria-label="Thatched-roof cottage with garden"></div>
      <h3 class="blog-title">Maecenas dignissim arcu</h3>
      <p class="blog-text">Aliquam sit amet faucibus maurisvivamus nibh risus, malesuada et ipsum in, iaculis feugiat quam vitae placerat consectetur..</p>
      <span class="read-more">Read more &gt;&gt;</span>
    </article>
    <article>
      <div class="blog-photo b3" role="img" aria-label="Chalet in front of mountains"></div>
      <h3 class="blog-title">Maecenas dignissim arcu</h3>
      <p class="blog-text">Aliquam sit amet faucibus maurisvivamus nibh risus, malesuada et ipsum in, iaculis feugiat quam vitae placerat consectetur..</p>
      <span class="read-more">Read more &gt;&gt;</span>
    </article>
  </div>
</section>

<footer class="site-footer">
  <div class="footer-col col-about">
    <h3>About us</h3>
    <p>Lorem ipsum dolor sit amet, consectetur adipiscing elit. Nunc at risus vitae quam pretium bibendum id id augue. In ullamcorper feugiat dui fermentum tincidunt.</p>
    <span class="read-more">Read more &gt;&gt;</span>
  </div>
  <div class="footer-col col-links">
    <h3>Quick links</h3>
    <ul>
      <li>Cottage by capacity</li>
      <li>Cottage by department</li>
      <li>Lodging by theme</li>
      <li>Blog</li>
      <li>Your Favorites</li>
    </ul>
  </div>
  <div class="footer-col col-signup">
    <h3>Email sign up</h3>
    <div class="signup-row">
      <div class="signup-input">Enter Email Address</div>
      <div class="signup-btn">Sign up</div>
    </div>
    <h3 class="follow">Follow us</h3>
    <div class="social"><span></span><span></span><span></span><span></span><span></span></div>
  </div>
</footer>
<div class="copyright">Copyright © 2019. Company Name. &nbsp;All Right Reserved</div>

</body>
</html>
```